TLK Electricial Contracting Services

Hi guys, after a design for my small electrical company, have logo design files to be incorporated into the layout, the basic concept is electrical contracting services for residential, commercial, industrial & data services, image is clean clear and strong,

Card format is to have a nice clean logo on front,with maybe the Residential – commercial – industrial - data, followed with licensed & insured, followed by contact details on backside of the card.

Target Market(s)

Residential, commercial, industrial sectors.

Industry/Entity Type

Electrical

Contact Information for Business Card

TLK logo,
Residential – commercial – industrial - data
REC: 61307
Email: tlk@vornamail.net.au
Phone: 0487 352 019

Requirements
Must have
• Clean & strong design.
Nice to have
• If possible, I would like the logo colours inverted so the text is orange and the background is black on the front of the card, then the backside of the card be the reverse colour
Should not have
• No Sparks, lightning bolts,

```html
<!DOCTYPE html>
<html lang="en">
<head>
<meta charset="utf-8">
<title>TLK Electricial Contracting Services – Business Card</title>
<link rel="stylesheet" href="https://fonts.googleapis.com/css2?family=Exo+2:wght@500;600;700&display=swap">
<style>
  :root {
    --page-bg: #f7f8fc;
    --brand-orange: #f4822b;
    --brand-black: #000000;
    --card-shadow: 6px 8px 10px rgba(0, 0, 0, 0.28);
    --type: "Exo 2", sans-serif;
  }
  * { box-sizing: border-box; margin: 0; padding: 0; }
  html, body {
    width: 1200px;
    height: 1000px;
    overflow: hidden;
    background: var(--page-bg);
    font-family: var(--type);
  }
  .canvas { position: relative; width: 1200px; height: 1000px; }

  .card {
    position: absolute;
    width: 735px;
    height: 419px;
    box-shadow: var(--card-shadow);
    overflow: hidden;
  }

  .brand { text-align: center; }
  .brand__name { font-weight: 700; line-height: 1; letter-spacing: 0.02em; }
  .brand__tagline { font-weight: 600; line-height: 1.2; }

  /* Front: black with orange brand */
  .card--front { left: 404px; top: 50px; background: var(--brand-black); color: var(--brand-orange); }
  .card--front .brand { position: absolute; left: 0; right: 0; top: 143px; }
  .card--front .brand__name { font-size: 84px; }
  .card--front .brand__tagline { font-size: 14px; margin-top: 4px; }

  .services {
    position: absolute;
    left: 0; right: 0; top: 327px;
    text-align: center;
    font-weight: 600;
    line-height: 21px;
  }
  .services__list { font-size: 16px; letter-spacing: 0.02em; }
  .services__badge { font-size: 17px; letter-spacing: 0.04em; }

  /* Back: orange with black details */
  .card--back { left: 61px; top: 500px; background: var(--brand-orange); color: var(--brand-black); }
  .card--back .edge-band {
    position: absolute; right: 0; top: 0;
    width: 27px; height: 100%;
    background: var(--brand-black);
  }
  .card--back .brand { position: absolute; left: 54px; top: 124px; width: 300px; }
  .card--back .brand__name { font-size: 130px; }
  .card--back .brand__tagline { font-size: 22px; margin-top: 4px; letter-spacing: 0.01em; }

  .contact { position: absolute; left: 406px; top: 158px; font-weight: 600; }
  .contact__licence { font-size: 22px; letter-spacing: 0.03em; line-height: 28px; margin-bottom: 4px; }
  .contact__row { display: flex; align-items: center; height: 35px; }
  .contact__icon { width: 32px; height: 26px; margin-left: 10px; margin-right: 24px; flex: none; }
  .contact__email { font-size: 21px; }
  .contact__phone { font-size: 25px; letter-spacing: 0.02em; }
</style>
</head>
<body>
<main class="canvas">

  <section class="card card--front" aria-label="Card front">
    <div class="brand">
      <div class="brand__name">TLK</div>
      <div class="brand__tagline">Tolan Lake Electrical</div>
    </div>
    <div class="services">
      <p class="services__list">residential - commercial - industrial - data</p>
      <p class="services__badge">LICENSED &amp; INSURED</p>
    </div>
  </section>

  <section class="card card--back" aria-label="Card back">
    <div class="brand">
      <div class="brand__name">TLK</div>
      <div class="brand__tagline">Tolan Lake Electrical</div>
    </div>

    <div class="contact">
      <p class="contact__licence">REC. 61307</p>
      <p class="contact__row">
        <svg class="contact__icon" viewBox="0 0 32 22" aria-hidden="true">
          <rect x="1" y="1" width="30" height="20" fill="none" stroke="#000" stroke-width="2"/>
          <path d="M1 1 L16 13 L31 1" fill="none" stroke="#000" stroke-width="2"/>
          <path d="M1 21 L12 10 M31 21 L20 10" fill="none" stroke="#000" stroke-width="2"/>
        </svg>
        <span class="contact__email">tlk@vornamail.net.au</span>
      </p>
      <p class="contact__row">
        <svg class="contact__icon" viewBox="0 0 32 32" aria-hidden="true">
          <path d="M8 3 L13 9 L10 13 C12 18 15 21 20 23 L24 20 L30 25 L26 30 C15 29 4 18 3 7 Z" fill="#000"/>
        </svg>
        <span class="contact__phone">0487 352 019</span>
      </p>
    </div>

    <div class="edge-band"></div>
  </section>

</main>
</body>
</html>
```